Letterhead Design for Law Firm

**Edit: I have added the photo of a bottom that I like.

------
We are looking for a re-design of our new letterhead. The letterhead is for a law firm and will be used for digital and traditionally printed correspondence.

Here are some suggestions:

- Please use colours are #8ec900 and simple black.
- Please do not use any type of "waves" at the bottom of the page. This is not in style at all.
- Please stay modern yet conservative.
- Please use font Segoe UI Light or similar if you can
- Avoid clipart or illustrations.
- Utilize ample white space in the layout so the design looks clean and information is easy to read at a glance. Don't overcrowd the letterhead.
- Make sure the letterhead design is consistent with our brand identity (see corvelith.ca)
-Please, no black headers or footers.

I am attaching my current letterhead and signature for your convenience.

Remember, the letterhead is an extension of our professional identity. We are a successful firm and trial lawyers who correspond with insurers, judges, lawyers, courts, clients, etc. Make it new, modern, attractive, yet powerful and conservative.

It needs to be easily printable. I would like the bleed removed in print so the black bar the bottom crosses the page (but the text is not near the edges)
Updates

Low design quality

Target Market(s)

Clients, Government Offices, Judiciary, Lawyers, Insurance Companies, Colleagues.

Industry/Entity Type

Law

Other font styles liked:
• Segoe UI LIght, Calibri Light,

Colors
00AB8E
00BBA5
67D7C9
C6EFE9
E9F9F6

Requirements
Must have
• Everything that is on the letterhead now.
Nice to have
• Cutting Edge design, yet conservative.
Should not have
• law firm cliche design, images,

```html
<!DOCTYPE html>
<html lang="en">
<head>
<meta charset="utf-8">
<title>Varenne Personal Injury Lawyers — Letterhead</title>
<link href="https://fonts.googleapis.com/css2?family=Open+Sans:wght@300;400;600;700&display=swap" rel="stylesheet">
<style>
  :root {
    --brand-green: #8ec900;
    --brand-black: #111111;
    --fold-grey: #4a4a4a;
    --ink: #1c1c1c;
    --rule: #7a7a7a;
    --paper: #ffffff;
    --backdrop: #e6e6e6;
    --sig-fill: #e4e4e4;
  }
  * { box-sizing: border-box; margin: 0; padding: 0; }
  html, body { width: 1200px; height: 874px; overflow: hidden; }
  body {
    background: var(--backdrop);
    font-family: "Open Sans", "Segoe UI", sans-serif;
    color: var(--ink);
    position: relative;
  }
  .letterhead {
    position: absolute;
    left: 310px; top: 27px;
    width: 580px; height: 820px;
    background: var(--paper);
    box-shadow: 0 2px 10px rgba(0,0,0,.12);
    overflow: hidden;
  }
  .header-bands, .footer-bands { position: absolute; left: 0; width: 580px; }
  .header-bands { top: 0; height: 70px; }
  .footer-bands { bottom: 0; height: 100px; }

  .firm-name {
    position: absolute; left: 34px; top: 20px;
    color: var(--paper);
    font-weight: 300; font-size: 24px; letter-spacing: 3px;
  }

  .contact-block {
    position: absolute; left: 394px; top: 34px;
    border-left: 1.5px solid var(--brand-green);
    padding-left: 9px;
    font-size: 6.6px; line-height: 1.45; font-weight: 400;
  }
  .contact-block b { font-weight: 700; }
  .contact-block .web-accent { color: var(--brand-green); font-weight: 700; }
  .contact-block .practice { margin-top: 6px; }

  .letter-body {
    position: absolute; left: 86px; top: 140px; width: 420px;
    font-size: 8.4px; line-height: 1.55; font-weight: 400;
  }
  .letter-body .bold { font-weight: 700; }
  .letter-body .gap { margin-top: 8px; }
  .subject {
    display: flex; gap: 0; margin-top: 10px;
    padding-bottom: 6px; border-bottom: 0.8px solid var(--rule);
  }
  .subject .label { width: 110px; font-weight: 700; }
  .subject .lines { font-weight: 600; }

  .sign-off {
    position: absolute; left: 300px; top: 565px;
    font-size: 8.4px; line-height: 1.5;
  }
  .sign-off .bold { font-weight: 700; }
  .signature {
    width: 120px; height: 34px; margin: 4px 0;
    background: var(--sig-fill); border-radius: 2px;
  }
</style>
</head>
<body>
  <main class="letterhead">
    <svg class="header-bands" viewBox="0 0 580 70" aria-hidden="true">
      <polygon points="0,12 360,12 346,58 0,58" fill="var(--brand-green)"/>
      <polygon points="318,0 500,0 480,22 336,22 332,50 318,54" fill="var(--brand-black)"/>
      <polygon points="318,54 332,50 352,50 346,58 318,58" fill="var(--fold-grey)"/>
    </svg>
    <div class="firm-name">VARENNE</div>

    <address class="contact-block">
      www.<span class="web-accent">CORVELITH</span>.ca<br>
      48 Harbour Street W., Suite 1210<br>
      Hamilton, ON&nbsp; L8P 2K7<br>
      <b>T:</b> 905-555-0142<br>
      <b>F:</b> 905-555-0187<br>
      <b>File Clerk:</b> Nora Whitcombe<br>
      <b>Email:</b> nora@corvelith.ca
      <div class="practice">
        <b>Practice Restricted</b><br>
        Serious Personal Injury<br>
        Wrongful Death Litigation<br>
        Long-Term Disability Litigation<br>
        Wrongful Dismissal Litigation<br>
        Employee Terminations
      </div>
    </address>

    <section class="letter-body">
      <p class="bold">Without Prejudice</p>
      <p class="gap">March 13, 2024</p>
      <p class="gap bold">By Email</p>
      <p class="gap">Northvale Insurance Company<br>
        Claims Litigation Department<br>
        250 Elmridge Road South<br>
        P.O. Box 3100<br>
        Waterloo, ON&nbsp;&nbsp; N2J 5T2</p>
      <p class="gap">Attention:&nbsp; Mr. Dorian Keller</p>
      <p class="gap">Mr. Keller:</p>
      <div class="subject">
        <span class="label">Re:</span>
        <span class="lines">Harlow v. Mercer et al.<br>
          DOL:&nbsp; September 12, 2019<br>
          Pre-Mediation Settlement Proposal – March 13<sup>th</sup>, 2024</span>
      </div>
    </section>

    <section class="sign-off">
      <p>Yours very truly,</p>
      <p class="bold">VARENNE PERSONAL INJURY LAWYERS</p>
      <div class="signature" role="img" aria-label="Handwritten signature of Paul D. Varenne"></div>
      <p>Paul D. Varenne</p>
      <p class="bold">Varenne Law Professional Corporation</p>
      <p>/nw</p>
      <p>Encl.</p>
    </section>

    <svg class="footer-bands" viewBox="0 0 580 100" aria-hidden="true">
      <polygon points="0,62 468,62 458,86 0,86" fill="var(--brand-green)"/>
      <polygon points="488,8 580,8 580,58 472,58" fill="var(--brand-black)"/>
    </svg>
  </main>
</body>
</html>
```